New Electrical Business Card Design

I would like a new design for my business cards.
i would like the same logo and font but new design
Please see attached files for front and back design.
large image can be used for graphics.
I would like the instagram link incorporated to back of card.
website site address needs to be changed to www.kestrelhillelectrical.au
everything else stays as is

```html
<!DOCTYPE html>
<html lang="en">
<head>
<meta charset="utf-8">
<title>Kestrel Hill Electrical &amp; Data – Business Card</title>
<link href="https://fonts.googleapis.com/css2?family=Poppins:wght@400;500;700&family=Oswald:wght@700&display=swap" rel="stylesheet">
<style>
  :root {
    --backdrop: #2b2b2c;
    --card-top: #1c1d1f;
    --card-bottom: #2c2d30;
    --text-light: #e4e5e6;
    --text-muted: #9a9c9f;
    --brand-green: #0f7a3b;
    --icon-green: #1c9a4c;
    --divider: #2aa5a0;
  }
  * { margin: 0; padding: 0; box-sizing: border-box; }
  html, body { width: 1200px; height: 1138px; overflow: hidden; }
  body {
    background: var(--backdrop);
    font-family: "Poppins", sans-serif;
    color: var(--text-light);
    position: relative;
  }
  .card {
    position: absolute;
    width: 621px;
    height: 376px;
    border-radius: 16px;
    background: linear-gradient(160deg, var(--card-top) 0%, var(--card-top) 45%, var(--card-bottom) 100%);
    overflow: hidden;
  }
  .card--front { left: 272px; top: 184px; }
  .card--back { left: 274px; top: 606px; }

  .wordmark {
    position: absolute;
    display: flex;
    align-items: center;
    gap: 12px;
    font-weight: 700;
    color: var(--text-light);
    text-transform: uppercase;
    white-space: nowrap;
  }
  .wordmark__dot {
    border-radius: 50%;
    background: var(--brand-green);
    flex: none;
  }
  .wordmark__name { line-height: 1.15; }

  .card--front .wordmark {
    left: 50%; top: 176px;
    transform: translate(-50%, -50%);
    font-size: 38px;
    letter-spacing: 1px;
    color: #b9bbbe;
  }
  .card--front .wordmark__dot { width: 22px; height: 22px; }
  .card--front .wordmark__sub { display: block; font-size: 17px; letter-spacing: 9px; }

  .services {
    position: absolute;
    left: 0; right: 0; top: 330px;
    text-align: center;
    font-size: 15.5px;
    color: var(--text-light);
  }
  .services__sep { color: var(--brand-green); margin: 0 8px; }

  .card--back .wordmark {
    left: 154px; top: 166px;
    transform: translate(-50%, -50%);
    font-size: 22px;
    letter-spacing: 0.5px;
  }
  .card--back .wordmark__dot { width: 14px; height: 14px; }
  .card--back .wordmark__sub { display: block; font-size: 10px; letter-spacing: 4.5px; }

  .divider {
    position: absolute;
    left: 306px; top: 82px;
    width: 1.5px; height: 176px;
    background: var(--divider);
  }
  .contact { position: absolute; left: 340px; top: 104px; }
  .contact__name {
    font-family: "Oswald", sans-serif;
    font-weight: 700;
    font-size: 22px;
    letter-spacing: 0.5px;
    text-transform: uppercase;
    margin-bottom: 12px;
  }
  .contact__first { color: var(--icon-green); }
  .contact__list { list-style: none; }
  .contact__item {
    display: flex; align-items: center; gap: 12px;
    font-size: 16px; height: 22.7px;
  }
  .contact__icon { width: 15px; height: 15px; flex: none; }

  .legal-band {
    position: absolute;
    left: 0; right: 0; bottom: 0; height: 50px;
    background: var(--brand-green);
    display: flex; align-items: center; justify-content: center; gap: 32px;
    font-size: 15px;
  }
  .legal-band__rule { width: 52px; height: 2px; background: linear-gradient(90deg, transparent, #fff 60%, transparent); }
</style>
</head>
<body>
  <section class="card card--front">
    <div class="wordmark">
      <span class="wordmark__dot"></span>
      <span class="wordmark__name">Kestrel Hill<span class="wordmark__sub">Electrical &amp; Data</span></span>
    </div>
    <p class="services">Residential<span class="services__sep">|</span>Commercial<span class="services__sep">|</span>Industrial<span class="services__sep">|</span>24hr Service</p>
  </section>

  <section class="card card--back">
    <div class="wordmark">
      <span class="wordmark__dot"></span>
      <span class="wordmark__name">Kestrel Hill<span class="wordmark__sub">Electrical &amp; Data</span></span>
    </div>
    <div class="divider"></div>
    <div class="contact">
      <h1 class="contact__name"><span class="contact__first">Daniel</span> Moravec</h1>
      <ul class="contact__list">
        <li class="contact__item">
          <svg class="contact__icon" viewBox="0 0 16 16" fill="none" stroke="#1c9a4c" stroke-width="1.3"><circle cx="8" cy="8" r="7"/><path d="M5.5 4.5l1.5 1.7-.8 1c.6 1.2 1.4 2 2.6 2.6l1-.8 1.7 1.5-.9 1c-2.9-.4-5.6-3.1-6-6z"/></svg>
          0400 555 182
        </li>
        <li class="contact__item">
          <svg class="contact__icon" viewBox="0 0 16 16" fill="none" stroke="#1c9a4c" stroke-width="1.3"><rect x="1" y="3" width="14" height="10" rx="1"/><path d="M1.5 3.5L8 9l6.5-5.5"/></svg>
          info@kestrelhillelectrical.au
        </li>
        <li class="contact__item">
          <svg class="contact__icon" viewBox="0 0 16 16" fill="none" stroke="#1c9a4c" stroke-width="1.2"><circle cx="8" cy="8" r="7"/><ellipse cx="8" cy="8" rx="3" ry="7"/><path d="M1 8h14M2 4.5h12M2 11.5h12"/></svg>
          www.kestrelhillelectrical.au
        </li>
        <li class="contact__item">
          <svg class="contact__icon" viewBox="0 0 16 16"><circle cx="8" cy="8" r="6.5" fill="#1c9a4c"/></svg>
          kestrel.hill.electrical
        </li>
      </ul>
    </div>
    <div class="legal-band">
      <span class="legal-band__rule"></span>
      <span>ABN: 51 824 753 556 &nbsp;|&nbsp; LIC No.: 412806C</span>
      <span class="legal-band__rule"></span>
    </div>
  </section>
</body>
</html>
```